Venture 482 - Lumora Book Cover

I am looking for a Lumora book cover for my book about "Venture 482".
The Book is Titled:
Venture 482 Ascended
Shaping Outcomes: Paths To Unlocking Cosmic Truths
Author is Dorian Pell
Here is a book description that may help you understand more about it:
Inspired by the genius of Edwin Marlowe, this comprehensive guide delves into the ancient wisdom and cutting-edge science behind the 482 method, a powerful tool for manifesting your desires. Whether you're seeking personal growth, financial success, or spiritual enlightenment, this book provides advanced techniques and methods to transform your dreams into reality.
Any questions please ask.
Thanks
Owen

```html
<!DOCTYPE html>
<html lang="en">
<head>
<meta charset="utf-8">
<title>Venture 482 Ascended — Book Cover</title>
<link rel="stylesheet" href="https://fonts.googleapis.com/css2?family=Bebas+Neue&family=Cinzel:wght@400&family=Tinos:wght@400;700&family=Montserrat:wght@500&display=swap">
<style>
  :root {
    --backdrop: #e9e9ea;
    --night-deep: #1d1328;
    --night-mid: #2f2140;
    --night-glow: #3e2c55;
    --ink-white: #f2f0f3;
    --author-blush: #f1ddd6;
    --emblem-light: #d9d4de;
    --emblem-dark: #2a1d38;
  }
  * { box-sizing: border-box; margin: 0; padding: 0; }
  html, body {
    width: 1200px;
    height: 1131px;
    overflow: hidden;
    background: var(--backdrop);
  }
  .cover {
    position: absolute;
    left: 250px;
    top: 37px;
    width: 700px;
    height: 1057px;
    overflow: hidden;
    background:
      radial-gradient(ellipse at 30% 8%, var(--night-glow) 0%, transparent 55%),
      radial-gradient(ellipse at 70% 60%, var(--night-mid) 0%, transparent 60%),
      var(--night-deep);
    color: var(--ink-white);
    text-align: center;
  }
  .cover__title {
    position: absolute;
    left: 0;
    right: 0;
    top: 140px;
    font-family: "Bebas Neue", "Arial Narrow", sans-serif;
    font-size: 150px;
    line-height: 1;
    letter-spacing: 2px;
    color: var(--ink-white);
  }
  .cover__emblem {
    position: absolute;
    left: 148px;
    top: 264px;
    width: 406px;
    height: 406px;
    border-radius: 50%;
    background: radial-gradient(circle, var(--emblem-dark) 0%, var(--emblem-dark) 52%, var(--emblem-light) 62%, #b9b2c2 80%, var(--emblem-light) 100%);
  }
  .cover__number {
    position: absolute;
    left: 0;
    right: 0;
    top: 422px;
    font-family: "Montserrat", sans-serif;
    font-weight: 500;
    font-size: 76px;
    line-height: 1;
    letter-spacing: 1px;
  }
  .cover__edition {
    position: absolute;
    left: 97px;
    right: 74px;
    top: 700px;
    display: flex;
    justify-content: space-between;
    font-family: "Bebas Neue", "Arial Narrow", sans-serif;
    font-size: 50px;
    line-height: 1;
  }
  .cover__subtitle {
    position: absolute;
    left: 0;
    right: 0;
    top: 812px;
    font-family: "Tinos", "Times New Roman", serif;
    font-size: 24px;
    line-height: 31px;
  }
  .cover__subtitle strong {
    display: block;
    font-weight: 700;
    text-transform: uppercase;
    letter-spacing: 0.2px;
  }
  .cover__author {
    position: absolute;
    left: 0;
    right: 0;
    top: 990px;
    font-family: "Cinzel", "Times New Roman", serif;
    font-weight: 400;
    font-size: 42px;
    line-height: 1;
    letter-spacing: 14px;
    color: var(--author-blush);
  }
</style>
</head>
<body>
  <main class="cover">
    <div class="cover__emblem" role="img" aria-label="Sacred geometry mandala with a crescent ring, eye motifs and star lines"></div>
    <h1 class="cover__title">VENTURE</h1>
    <div class="cover__number">482</div>
    <div class="cover__edition" aria-label="Ascended">
      <span>A</span><span>S</span><span>C</span><span>E</span><span>N</span><span>D</span><span>E</span><span>D</span>
    </div>
    <p class="cover__subtitle">
      <strong>Shaping Outcomes:</strong>
      Paths to unlocking<br>cosmic truths
    </p>
    <p class="cover__author">DORIAN PELL</p>
  </main>
</body>
</html>
```